VELMA, an e-commerce website with a twist, providing consumer-to-consumer and business-to-consumer sa

I have only uploaded 10 wire-frame pages of the website. These pages have been chosen for the different lay-outs and should give an idea of what will be needed. There are many more that I won’t upload yet, I aim to choose a winner first then there will be a high possibility that the winner will get the chance to do the design work for these later.
The design I have in mind is to keep it clean and easy with no/minimal fancy fonts and hieroglyphics. The logo is white with an orange highlight on a solid background of black, please note that the logo is white on a black background and is not a black box with white lettering, trust that makes sense. I like the idea of the top part of the website being black all the way across. I don’t see the need for more than 3 colours in the actual base website (the pictures and adverts added by users will add other colours). Although orange is the highlight colour in the logo I am open to suggestions on this, so long as the highlight colour features throughout the site.

Website width is 1220px, all pages in the PDF are 1220px

Logo font is Rezlong

The company is going to be like tradu, but much more focused on raising money for charity and humanitarian relief.

Target Market(s)

the modern era of smartphones and the sharing community

Industry/Entity Type

Business

Number of Pages Required

5+ page

Font styles to use
Sans Serif
Other font styles liked:
• rezlong

Colors
faa54b
f78f20
ffffff
000000
fbfbfb
f5f5f5

Requirements
Nice to have
• Although orange is the highlight colour in the logo I am open to suggestions on this, so long as the highlight colour features throughout the site.

```html
<!DOCTYPE html>
<html lang="en">
<head>
<meta charset="utf-8">
<title>VELMA – Home</title>
<link href="https://fonts.googleapis.com/css2?family=Lato:wght@400;700&display=swap" rel="stylesheet">
<style>
:root{
  --orange:#f78f20;
  --orange-soft:#faa54b;
  --black:#000;
  --white:#fff;
  --panel:#fbfbfb;
  --line:#d8d8d8;
  --text:#333;
  --muted:#555;
}
*{margin:0;padding:0;box-sizing:border-box}
html,body{width:736px;height:1200px;overflow:hidden;background:var(--white)}
body{position:relative;font-family:'Lato',Arial,sans-serif;color:var(--text)}
.abs{position:absolute}
.topbar{left:0;top:0;width:736px;height:26px;background:var(--black);border-bottom:1px solid #333;color:var(--white);font-size:8px;letter-spacing:.2px}
.topbar span{position:absolute;top:8px}
.header{left:0;top:26px;width:736px;height:70px;background:var(--black);color:var(--white)}
.logo{left:40px;top:10px;font-size:38px;font-weight:700;letter-spacing:-1px;line-height:40px}
.logo b{color:var(--orange)}
.header .nav{font-size:10px;position:absolute}
.media{background:linear-gradient(135deg,#3c3238,#8a6f66);}
.media-bar{position:absolute;left:0;bottom:0;width:100%;height:8px;background:#111}
.media-bar i{position:absolute;left:22px;right:30px;top:3px;height:2px;background:#555}
.play{position:absolute;left:50%;top:45%;width:26px;height:26px;margin:-13px;border:3px solid var(--white);border-radius:50%}
.play:after{content:"";position:absolute;left:8px;top:5px;border-left:9px solid var(--white);border-top:5px solid transparent;border-bottom:5px solid transparent}
.search{left:254px;top:112px;width:214px;height:256px;background:var(--orange-soft)}
.search h2{height:36px;background:var(--orange);color:var(--white);font-size:13px;font-weight:400;text-align:center;line-height:36px}
.field{position:absolute;background:var(--white);height:28px;font-size:7px;color:#999;padding:10px 12px}
.search label{position:absolute;left:13px;font-size:8px;color:#555}
.search .btn{position:absolute;left:12px;top:206px;width:190px;height:31px;background:var(--black);color:var(--white);font-size:11px;text-align:center;line-height:31px}
.product{left:496px;width:200px;height:80px;border:1px solid var(--line);background:var(--white)}
.product .thumb{position:absolute;left:10px;top:10px;width:60px;height:60px;background:linear-gradient(135deg,#eee,#bbb)}
.product h3{position:absolute;left:86px;top:11px;font-size:9.5px;font-weight:700;color:#111}
.product p{position:absolute;left:86px;top:28px;width:104px;font-size:6.8px;line-height:9.6px;color:#222}
.rule{left:40px;width:656px;height:1px;background:var(--line)}
.banner{left:40px;width:656px;height:100px}
.banner .title{position:absolute;color:var(--white);font-size:24px;letter-spacing:.5px}
.buy{position:absolute;width:97px;height:28px;background:var(--orange);color:var(--white);font-size:10px;text-align:center;line-height:28px}
.section-title{left:40px;font-size:13.5px;font-weight:700;color:#444}
.review{width:190px}
.review h4{font-size:10px;font-weight:400;color:#444}
.stars{margin:5px 0 8px;color:var(--orange);font-size:10px;letter-spacing:1px}
.review p{font-size:7.2px;line-height:9.6px;color:#444}
.feedback-link{left:548px;top:678px;font-size:7.4px;color:var(--orange);text-decoration:underline}
.charity{border:1px solid var(--line);background:var(--white);display:flex;align-items:center;justify-content:center;font-size:10px;font-weight:700;color:#333;text-align:center}
.promo{left:337px;width:359px}
.promo-text{position:absolute;color:var(--white);font-size:9.5px;font-weight:700;line-height:10px}
.footer{top:1174px;font-size:7.6px;color:#222}
.social{top:1152px;width:10px;height:10px;background:#111;border-radius:2px}
</style>
</head>
<body>

<div class="abs topbar">
  <span style="left:40px">NOTIFICATIONS &nbsp;&nbsp;| &nbsp;&nbsp;NEWS &nbsp;&nbsp;| &nbsp;&nbsp;LIST ITEM</span>
  <span style="left:422px">CONTACT US &nbsp;&nbsp;| &nbsp;&nbsp;HELP &nbsp;&nbsp;| &nbsp;&nbsp;TERMS AND CONDITIONS &nbsp;&nbsp;| &nbsp;&nbsp;<svg width="7" height="7" viewBox="0 0 10 10" style="vertical-align:-1px"><circle cx="4" cy="4" r="3" fill="none" stroke="#fff" stroke-width="1.6"/><line x1="6.3" y1="6.3" x2="9.5" y2="9.5" stroke="#fff" stroke-width="1.6"/></svg> SEARCH</span>
</div>

<header class="abs header">
  <div class="abs logo">VEL<b>M</b>A</div>
  <div class="nav" style="left:612px;top:16px"><svg width="11" height="9" viewBox="0 0 11 9" style="vertical-align:-1px"><path d="M0 1h2l1.5 5h6L11 2H3" fill="none" stroke="#f78f20" stroke-width="1.4"/><circle cx="4" cy="8" r="1" fill="#f78f20"/><circle cx="9" cy="8" r="1" fill="#f78f20"/></svg> &nbsp;&nbsp;| &nbsp;&nbsp;WISH LIST</div>
  <div class="nav" style="left:450px;top:42px">SIGN IN &nbsp;&nbsp;| &nbsp;&nbsp;MY ACCOUNT &nbsp;&nbsp;| &nbsp;&nbsp;MY RECENT SEARCHES</div>
</header>

<div class="abs media" style="left:40px;top:112px;width:186px;height:118px" role="img" aria-label="Video still: woman smiling, showing a wristwatch"><div class="play"></div><div class="media-bar"><i></i></div></div>
<div class="abs media" style="left:40px;top:250px;width:186px;height:116px;background:linear-gradient(135deg,#2b2b30,#6d6a70)" role="img" aria-label="Video still: laptop on a desk showing a woman with a flower"><div class="play"></div><div class="media-bar"><i></i></div></div>

<form class="abs search">
  <h2>SEARCH YOUR PRODUCTS</h2>
  <div class="field" style="left:12px;top:53px;width:190px">Item</div>
  <div class="field" style="left:12px;top:89px;width:190px">Location</div>
  <label style="top:136px">From</label>
  <div class="field" style="left:68px;top:126px;width:134px">€</div>
  <label style="top:172px">To</label>
  <div class="field" style="left:68px;top:162px;width:134px">€</div>
  <div class="btn">SEARCH</div>
</form>

<div class="abs product" style="top:113px"><div class="thumb" role="img" aria-label="Product photo: wristwatch"></div><h3>Product Name</h3><p>Lorem Ipsum is simply dummy text of the printing and typesetting industry. Lorem Ipsum has been</p></div>
<div class="abs product" style="top:201px"><div class="thumb" role="img" aria-label="Product photo: smartwatch"></div><h3>Product Name</h3><p>Lorem Ipsum is simply dummy text of the printing and typesetting industry. Lorem Ipsum has been</p></div>
<div class="abs product" style="top:288px"><div class="thumb" style="background:linear-gradient(135deg,#d04a9a,#5a4ac8)" role="img" aria-label="Product photo: colourful tablets"></div><h3>Product Name</h3><p>Lorem Ipsum is simply dummy text of the printing and typesetting industry. Lorem Ipsum has been</p></div>

<div class="abs rule" style="top:390px"></div>

<div class="abs banner" style="top:408px;background:linear-gradient(90deg,#4a1a10 0%,#5a2414 40%,#555 41%,#7a6a62 100%)" role="img" aria-label="Advert: woman in red sunglasses">
  <div class="title" style="left:40px;top:36px">LOREM IPSUM</div>
  <div class="buy" style="left:238px;top:36px">BUY NOW</div>
</div>

<div class="abs rule" style="top:526px"></div>
<h2 class="abs section-title" style="top:541px">USER FEEDBACK</h2>

<div class="abs review" style="left:50px;top:576px"><h4>OWEN CALLOWAY</h4><div class="stars">★★★★★</div><p>Lorem Ipsum is simply dummy text of the printing and typesetting industry. Lorem Ipsum has been the industry's standard dummy text ever since the 1500s, when an unknown printer took a galley of type and</p></div>
<div class="abs review" style="left:270px;top:576px"><h4>NORA PEMBROOK</h4><div class="stars">★★★★★</div><p>Lorem Ipsum is simply dummy text of the printing and typesetting industry. Lorem Ipsum has been the industry's standard dummy text ever since the 1500s, when an unknown printer took a galley of type and</p></div>
<div class="abs review" style="left:491px;top:576px"><h4>LILA ASHCROFT</h4><div class="stars">★★★★★</div><p>Lorem Ipsum is simply dummy text of the printing and typesetting industry. Lorem Ipsum has been the industry's standard dummy text ever since the 1500s, when an unknown printer took a galley of type and</p></div>
<a class="abs feedback-link">Leave Feedback for a chance to win a prize</a>

<div class="abs rule" style="top:709px"></div>

<div class="abs banner" style="top:724px;background:linear-gradient(90deg,#5a3a22,#9a6a40 50%,#6a4628)" role="img" aria-label="Advert: wristwatch, keys and leather accessories on a table">
  <div class="title" style="left:180px;top:36px">LOREM IPSUM</div>
  <div class="buy" style="left:378px;top:36px">BUY NOW</div>
</div>

<div class="abs rule" style="top:845px"></div>
<h2 class="abs section-title" style="top:863px">CHARITIES SUPPORTED</h2>

<div class="abs charity" style="left:41px;top:894px;width:92px;height:128px">Larkwood Property</div>
<div class="abs charity" style="left:138px;top:894px;width:92px;height:60px">Northgate</div>
<div class="abs charity" style="left:138px;top:958px;width:92px;height:64px">Trailmark</div>
<div class="abs charity" style="left:236px;top:894px;width:78px;height:44px">Brightfold</div>
<div class="abs charity" style="left:236px;top:942px;width:78px;height:80px">Sunridge</div>
<div class="abs charity" style="left:41px;top:1028px;width:61px;height:90px">Peakwave</div>
<div class="abs charity" style="left:107px;top:1028px;width:62px;height:90px">Lumen Audio</div>
<div class="abs charity" style="left:174px;top:1028px;width:61px;height:90px">Vitalis</div>
<div class="abs charity" style="left:240px;top:1028px;width:74px;height:90px">Corvo</div>

<div class="abs promo" style="top:894px;height:108px;background:linear-gradient(90deg,#3a3430,#6a5a4c 60%,#4a4038)" role="img" aria-label="Advert: man with a wristwatch sitting outdoors">
  <div class="promo-text" style="left:73px;top:42px;width:130px">Lorem Ipsum is simply dummy text of the printing and typesetting industry</div>
  <div class="abs" style="left:215px;top:40px;width:80px;height:28px;background:#1a1a1a;color:#fff;font-size:10px;text-align:center;line-height:28px">BUY NOW</div>
</div>
<div class="abs promo" style="top:1012px;height:106px;background:#8a7420">
  <div class="abs" style="left:30px;top:0;width:128px;height:106px;background:linear-gradient(135deg,#6a6a6a,#2c2c2c)" role="img" aria-label="Photo: man in a suit checking his watch"></div>
  <div class="abs" style="left:203px;top:47px;font-size:10px;color:#2a2410">LOREM IPSUM</div>
</div>

<div class="abs rule" style="top:1142px"></div>
<div class="abs social" style="left:589px"></div>
<div class="abs social" style="left:605px"></div>
<div class="abs social" style="left:621px"></div>
<div class="abs social" style="left:637px"></div>
<div class="abs social" style="left:653px"></div>
<div class="abs social" style="left:669px"></div>
<div class="abs social" style="left:685px"></div>

<nav class="abs footer" style="left:40px">About Velma &nbsp;&nbsp;| &nbsp;&nbsp;Safety Hub &nbsp;&nbsp;| &nbsp;&nbsp;Resolution Hub &nbsp;&nbsp;| &nbsp;&nbsp;Vendor Hub &nbsp;&nbsp;| &nbsp;&nbsp;Partner Hub &nbsp;&nbsp;| &nbsp;&nbsp;Charity Hub</nav>
<nav class="abs footer" style="left:583px">Advertise on Hub &nbsp;&nbsp;| &nbsp;&nbsp;Site map &nbsp;&nbsp;&nbsp;&nbsp; C24</nav>

</body>
</html>
```